Plakat für Verein
Zielgruppe
Wir möchten eine Veranstaltung für unseren Verein - Hinterbrunnwalder Kameradschaftsbund machen.
Aufgabenstellung
Die Party der Golden 20er
Glanz-Glamour-Lebenslust
Tanzen wie früher - Feiern wie nie
21. März - Uhrzeit: 20.30 im Saal KT
Live mit DJaneWaltraud
Dresscode: Goldene 20er - Fransen, Federn, Hosenträger, Zylinder
Farbe: Gold/Schgwarz

```html
<!DOCTYPE html>
<html lang="de">
<head>
<meta charset="utf-8">
<title>Die Party der Golden 20er</title>
<link rel="stylesheet" href="https://fonts.googleapis.com/css2?family=Comfortaa:wght@400;700&family=Monoton&family=Plus+Jakarta+Sans:wght@300;700&display=swap">
<style>
  :root {
    --black: #050505;
    --white: #ffffff;
    --gold-light: #d9b66a;
    --gold: #9a7330;
    --gold-deep: #3d2a0e;
  }
  html, body {
    margin: 0;
    padding: 0;
    overflow: hidden;
    background: var(--black);
  }
  .poster {
    position: relative;
    width: 849px;
    height: 1200px;
    overflow: hidden;
    background: var(--black);
    color: var(--white);
    text-align: center;
  }
  .champagne-photo {
    position: absolute;
    left: 0;
    top: 0;
    width: 849px;
    height: 1200px;
    background:
      radial-gradient(ellipse 55% 50% at 68% 72%, var(--gold-light) 0%, var(--gold) 35%, var(--gold-deep) 65%, rgba(5,5,5,0) 100%);
  }
  .tagline {
    position: absolute;
    top: 15px;
    left: 0;
    width: 100%;
    margin: 0;
    font: 700 29px/1.2 "Comfortaa", sans-serif;
  }
  .headline {
    position: absolute;
    top: 58px;
    left: 0;
    width: 100%;
    margin: 0;
    font: 400 80px/1.2 "Monoton", sans-serif;
    letter-spacing: 0;
    word-spacing: 10px;
    text-transform: uppercase;
  }
  .motto {
    position: absolute;
    top: 266px;
    left: 0;
    width: 100%;
    margin: 0;
    font: 400 44px/1.2 "Comfortaa", sans-serif;
  }
  .artist {
    position: absolute;
    top: 397px;
    left: 0;
    width: 100%;
    margin: 0;
    font: 700 34px/1.2 "Comfortaa", sans-serif;
  }
  .club {
    position: absolute;
    top: 940px;
    left: 0;
    width: 100%;
    display: flex;
    flex-direction: column;
    align-items: center;
    gap: 18px;
  }
  .club-dot {
    width: 58px;
    height: 58px;
    border-radius: 50%;
    background: var(--white);
  }
  .club-name {
    margin: 0;
    font: 700 16px/1.4 "Comfortaa", sans-serif;
    text-transform: uppercase;
  }
  .event-details {
    position: absolute;
    top: 1085px;
    left: 0;
    width: 100%;
    margin: 0;
    font: 700 33px/1.2 "Plus Jakarta Sans", sans-serif;
    text-transform: uppercase;
  }
  .dresscode {
    position: absolute;
    top: 1123px;
    left: 0;
    width: 100%;
    margin: 0;
    font: 300 20px/1.2 "Plus Jakarta Sans", sans-serif;
  }
</style>
</head>
<body>
  <main class="poster">
    <div class="champagne-photo" role="img" aria-label="Foto: Sektglas mit goldenem, perlendem Champagner vor schwarzem Hintergrund"></div>

    <p class="tagline">Tanzen wie früher - Feiern wie nie!</p>
    <h1 class="headline">Die Party der<br>Golden 20er</h1>
    <p class="motto">Glanz - Glamour - Lebenslust</p>
    <p class="artist">Live mit DJane Waltraud</p>

    <div class="club">
      <span class="club-dot"></span>
      <p class="club-name">Hinterbrunnwalder<br>Kameradschaftsbund</p>
    </div>

    <p class="event-details">21. März - Uhrzeit: 20:30 im Saal KT</p>
    <p class="dresscode">Dresscode: Goldene 20er - Fransen, Federn, Hosenträger, Zylinder</p>
  </main>
</body>
</html>
```